Company identity deisgn should support 2 languages

I would like to get our company identity design
This includes the following only
Business Cards 2 languages Arabic and English
Email signature
Letterhead
Linkedin profile images
Attached is the logo in Ai format

Requirements
Must have
• For business card
Must have
Name and Adrees in arabic
Name and Address in english
You might use both side of the card
Should not have
• Any pictures other than the logo

```html
<!DOCTYPE html>
<html lang="en">
<head>
<meta charset="utf-8">
<title>Lumen Cognitive Systems — Business Card</title>
<link rel="stylesheet" href="https://fonts.googleapis.com/css2?family=Open+Sans:wght@400;600;700&family=Tajawal:wght@400;500;700&display=swap">
<style>
  :root {
    --brand-blue: #1f6fb5;
    --text-grey: #555a5f;
    --muted-grey: #8a8f94;
    --rule-grey: #c9cccf;
    --paper: #ffffff;
  }
  * { margin: 0; padding: 0; box-sizing: border-box; }
  html, body { width: 1200px; height: 578px; overflow: hidden; background: var(--paper); }
  .card {
    position: relative; width: 1200px; height: 578px;
    background: var(--paper);
    font-family: "Open Sans", Arial, sans-serif;
    color: var(--text-grey);
  }
  .brand {
    position: absolute; left: 300px; top: 84px;
    display: flex; align-items: center; gap: 28px;
  }
  .brand-square { width: 72px; height: 72px; background: var(--brand-blue); }
  .brand-name {
    font-size: 42px; font-weight: 600; letter-spacing: 2px;
    color: var(--brand-blue); text-transform: uppercase; white-space: nowrap;
  }
  .divider {
    position: absolute; left: 615px; top: 220px;
    width: 2px; height: 195px; background: var(--rule-grey);
  }
  .address { position: absolute; right: 620px; top: 240px; width: 520px; }
  .address-ar {
    font-family: "Tajawal", Arial, sans-serif; direction: rtl; text-align: right;
    font-size: 28px; line-height: 44px; color: var(--text-grey);
  }
  .address-en {
    margin-top: 18px; padding-left: 215px;
    font-size: 26px; line-height: 42px; color: var(--text-grey);
  }
  .person { position: absolute; left: 660px; top: 244px; }
  .person-name-en {
    font-size: 40px; font-weight: 700; color: var(--brand-blue); letter-spacing: 0.5px; line-height: 48px;
  }
  .person-title-en { font-size: 28px; color: var(--muted-grey); line-height: 38px; }
  .person-name-ar, .person-title-ar {
    font-family: "Tajawal", Arial, sans-serif; direction: rtl; text-align: left; unicode-bidi: plaintext;
  }
  .person-name-ar { font-size: 40px; font-weight: 700; color: var(--brand-blue); line-height: 48px; }
  .person-title-ar { font-size: 28px; color: var(--muted-grey); line-height: 38px; }
  .contacts {
    position: absolute; left: 42px; right: 60px; top: 444px;
    display: flex; justify-content: space-between; align-items: center;
    font-size: 25px; color: var(--text-grey);
  }
  .contact { display: flex; align-items: center; gap: 6px; white-space: nowrap; }
  .contact svg { width: 26px; height: 26px; fill: var(--brand-blue); flex: none; }
  .web-band {
    position: absolute; left: 0; top: 498px; width: 1200px; height: 42px;
    background: var(--brand-blue);
  }
  .web-address {
    position: absolute; left: 238px; top: 4px;
    font-size: 25px; font-weight: 600; letter-spacing: 3px; color: var(--paper); text-transform: uppercase;
  }
</style>
</head>
<body>
<main class="card">
  <header class="brand">
    <div class="brand-square"></div>
    <div class="brand-name">Lumen Cognitive Systems</div>
  </header>

  <section class="address">
    <p class="address-ar">2140 طريق سيدار هولو<br>فيربانكس، ألاسكا 99701</p>
    <p class="address-en">2140 Cedar Hollow Road<br>Fairbanks, Alaska 99701</p>
  </section>

  <div class="divider"></div>

  <section class="person">
    <h1 class="person-name-en">DANIEL HARPER</h1>
    <p class="person-title-en">President</p>
    <p class="person-name-ar">دانيال هاربر</p>
    <p class="person-title-ar">رئيس</p>
  </section>

  <section class="contacts">
    <span class="contact">
      <svg viewBox="0 0 24 24"><path d="M6.6 10.8a15.1 15.1 0 0 0 6.6 6.6l2.2-2.2c.3-.3.7-.4 1-.2 1.1.4 2.3.6 3.6.6.6 0 1 .4 1 1V20c0 .6-.4 1-1 1A17 17 0 0 1 3 4c0-.6.4-1 1-1h3.5c.6 0 1 .4 1 1 0 1.3.2 2.5.6 3.6.1.3 0 .7-.2 1z"/></svg>
      555-210-4836
    </span>
    <span class="contact">
      <svg viewBox="0 0 24 24"><path d="M7 1h10a2 2 0 0 1 2 2v18a2 2 0 0 1-2 2H7a2 2 0 0 1-2-2V3a2 2 0 0 1 2-2zm0 3v14h10V4zm5 15.2a1.2 1.2 0 1 0 0 2.4 1.2 1.2 0 0 0 0-2.4z"/></svg>
      555-618-2790
    </span>
    <span class="contact">
      <svg viewBox="0 0 24 24"><path d="M6 2h9l3 3v4H6zm-2 8h16a2 2 0 0 1 2 2v6h-4v4H6v-4H2v-6a2 2 0 0 1 2-2zm4 7v3h8v-3zm10-5a1 1 0 1 0 0 2 1 1 0 0 0 0-2z"/></svg>
      555-347-1562
    </span>
    <span class="contact">
      <svg viewBox="0 0 24 24"><path d="M2 5h20v14H2zm2 2v.5l8 5 8-5V7zm0 2.8V17h16V9.8l-8 5z"/></svg>
      info@lumencognitive.com
    </span>
  </section>

  <footer class="web-band">
    <span class="web-address">www.lumencognitive.com</span>
  </footer>
</main>
</body>
</html>
```